Brindle Yard Care. The best in the biz

I run a lawn care service that offers full service mowing. 100% satisfaction guarantee. Fast, Friendly, quality service "I am your lawns best friend" I cut residential lawns. I offer a mow package that includes trimming, edging and clean up. Prices very from 20 dollars to 75. I want my logo to stand out. Free estimates

Target Market(s)

Home owners

Industry/Entity Type

Landscaping

Contact Information for Business Card

555-812-4473 tomvale48@quillmail.net Derek. Brindle Yard care

Colors
f37122
9bcb3c
cadf82

Requirements
Must have
• Company name.
• Phone number
• Email
• My services
• images
Nice to have
• A sun that is growing grass.
Should not have
• Incorrect information

```html
<!DOCTYPE html>
<html lang="en">
<head>
<meta charset="utf-8">
<title>Brindle Yard Care – Business Card</title>
<link rel="stylesheet" href="https://fonts.googleapis.com/css2?family=Open+Sans:wght@400;600;700&display=swap">
<style>
  :root {
    --backdrop: #3b3633;
    --card: #121212;
    --green: #1f9a48;
    --orange: #f39422;
    --white: #f2f2f2;
  }
  * { margin: 0; padding: 0; box-sizing: border-box; }
  html, body {
    width: 1200px;
    height: 844px;
    overflow: hidden;
    background: var(--backdrop);
    font-family: "Open Sans", Arial, sans-serif;
  }
  .sheet {
    position: relative;
    width: 1200px;
    height: 844px;
  }
  .card {
    position: absolute;
    top: 272px;
    width: 530px;
    height: 303px;
    background: var(--card);
    border-radius: 4px;
    box-shadow: 0 10px 28px rgba(0,0,0,.45);
    overflow: hidden;
  }
  .card--front { left: 45px; }
  .card--back  { left: 625px; }

  .brand {
    display: flex;
    align-items: center;
    gap: 12px;
    color: var(--green);
    font-weight: 700;
    font-size: 34px;
    letter-spacing: .5px;
    white-space: nowrap;
  }
  .brand__dot {
    width: 26px;
    height: 26px;
    border-radius: 50%;
    background: var(--orange);
    flex: none;
  }

  /* front */
  .card--front .brand { position: absolute; left: 40px; top: 88px; }
  .contact {
    position: absolute;
    right: 30px;
    top: 158px;
    text-align: right;
    color: var(--white);
    font-size: 15px;
    line-height: 26px;
  }
  .contact__name {
    display: flex;
    align-items: center;
    justify-content: flex-end;
    gap: 8px;
    color: var(--orange);
    font-weight: 700;
    font-size: 16px;
  }
  .contact__name::after {
    content: "";
    width: 18px;
    height: 2px;
    background: var(--orange);
  }
  .contact__row {
    display: flex;
    align-items: center;
    justify-content: flex-end;
    gap: 10px;
  }
  .contact__row svg { width: 14px; height: 14px; fill: var(--orange); flex: none; }
  .rule {
    position: absolute;
    height: 2px;
    background: var(--orange);
  }
  .rule--name   { left: 40px; right: 102px; top: 170px; }
  .rule--bottom { left: 0; right: 0; top: 258px; }

  /* back */
  .card--back {
    display: flex;
    flex-direction: column;
    align-items: center;
    text-align: center;
    padding-top: 70px;
  }
  .pledge {
    margin-top: 44px;
    color: var(--orange);
    font-weight: 700;
    font-size: 16px;
  }
  .qualities {
    margin-top: 6px;
    color: var(--white);
    font-size: 14px;
    font-weight: 600;
  }
  .qualities span { margin: 0 6px; }
  .motto {
    margin-top: 14px;
    color: var(--green);
    font-weight: 600;
    font-size: 17px;
  }
</style>
</head>
<body>
<main class="sheet">
  <section class="card card--front" aria-label="Business card front">
    <div class="brand"><span class="brand__dot"></span>Brindle Yard Care</div>
    <div class="rule rule--name"></div>
    <div class="contact">
      <p class="contact__name">Derek</p>
      <p class="contact__row">555-812-4473
        <svg viewBox="0 0 24 24" aria-hidden="true"><path d="M6.6 10.8a15.1 15.1 0 0 0 6.6 6.6l2.2-2.2a1 1 0 0 1 1-.25 11.4 11.4 0 0 0 3.6.57 1 1 0 0 1 1 1V20a1 1 0 0 1-1 1A17 17 0 0 1 3 4a1 1 0 0 1 1-1h3.5a1 1 0 0 1 1 1c0 1.25.2 2.45.57 3.6a1 1 0 0 1-.25 1z"/></svg>
      </p>
      <p class="contact__row">tomvale48@quillmail.net
        <svg viewBox="0 0 24 24" aria-hidden="true"><path d="M2 5h20v14H2z M2 5l10 8 10-8" fill="var(--orange)" stroke="var(--card)" stroke-width="1.5"/></svg>
      </p>
    </div>
    <div class="rule rule--bottom"></div>
  </section>

  <section class="card card--back" aria-label="Business card back">
    <div class="brand"><span class="brand__dot"></span>Brindle Yard Care</div>
    <p class="pledge">100% satisfaction guarantee.</p>
    <p class="qualities">Fast<span>|</span>Friendly<span>|</span>Quality Service</p>
    <p class="motto">I am your Lawns Best Friend</p>
  </section>
</main>
</body>
</html>
```